Business Card Design Project

Doctor, Pain Management. Need a new business card design with appointment info on the back. New address is 18 Corvell Road, Suite 304, Brisdale, NJ 07391. Right now I believe the rest of the information is staying the same.

```html
<!DOCTYPE html>
<html lang="en">
<head>
<meta charset="utf-8">
<title>Meridian Pain Care – Business Card</title>
<link href="https://fonts.googleapis.com/css2?family=Open+Sans:wght@400;600;700&family=Arimo:wght@400&display=swap" rel="stylesheet">
<style>
  :root {
    --backdrop: #e6e7e9;
    --card: #ffffff;
    --ink: #1c1c1c;
    --muted: #8a8a8a;
    --rule: #9a9a9a;
    --accent: #ec5a10;
    --dark-1: #7d8790;
    --dark-2: #1a1d21;
    --dark-3: #050607;
  }
  * { margin: 0; padding: 0; box-sizing: border-box; }
  html, body { width: 1200px; height: 782px; overflow: hidden; }
  body {
    background: var(--backdrop);
    font-family: "Open Sans", Arial, sans-serif;
    color: var(--ink);
    position: relative;
  }
  .card {
    position: absolute;
    top: 236px;
    width: 540px;
    height: 309px;
    background: var(--card);
    overflow: hidden;
    box-shadow: 0 6px 18px rgba(0,0,0,.18);
  }
  .card--front { left: 40px; }
  .card--back { left: 620px; }

  /* Front */
  .front-shape { position: absolute; inset: 0; }
  .front-illustration {
    position: absolute; left: 0; top: 0; width: 250px; height: 130px;
    background:
      radial-gradient(ellipse 30px 55px at 128px 80px, rgba(255,120,30,.85), rgba(255,120,30,0) 100%),
      radial-gradient(ellipse 110px 90px at 125px 70px, #3a2a2a, rgba(58,42,42,0) 100%),
      linear-gradient(90deg, #8b959e, #59626b 70%, rgba(60,66,72,0));
  }
  .company-name {
    position: absolute; left: 282px; top: 84px;
    font-family: "Arimo", Arial, sans-serif;
    font-size: 23px; color: var(--accent); letter-spacing: .3px;
  }
  .contact-list {
    position: absolute; left: 20px; top: 142px; list-style: none;
    font-size: 13px; line-height: 19px;
  }
  .contact-list li { display: flex; align-items: center; gap: 5px; }
  .contact-list svg { width: 10px; height: 10px; fill: var(--accent); flex: none; }
  .doctor {
    position: absolute; right: 26px; top: 220px; text-align: right;
  }
  .doctor-name { font-size: 16px; font-weight: 700; color: var(--accent); letter-spacing: .3px; line-height: 20px; }
  .doctor-title { font-size: 13px; line-height: 18px; }
  .address { margin-top: 10px; font-size: 13px; line-height: 18px; }

  /* Back */
  .appointment-title {
    position: absolute; left: 196px; top: 28px;
    font-size: 17px; font-weight: 600; letter-spacing: .6px;
  }
  .field {
    position: absolute; left: 22px; width: 332px;
    font-size: 14px; color: var(--muted); letter-spacing: .3px;
    border-bottom: 1px solid var(--rule); padding-bottom: 2px;
  }
  .field--name { top: 50px; }
  .field--date { top: 86px; }
  .field--time { top: 122px; }
  .notice {
    position: absolute; left: 22px; top: 156px; width: 332px;
    font-size: 10px; line-height: 13px; color: var(--muted); text-align: center;
  }
  .back-illustration {
    position: absolute; right: 0; top: 0; width: 190px; height: 309px;
    background:
      radial-gradient(ellipse 26px 110px at 120px 170px, rgba(255,120,30,.9), rgba(255,120,30,0) 100%),
      radial-gradient(ellipse 95px 160px at 115px 175px, #2c2f3a, rgba(44,47,58,0) 100%),
      linear-gradient(90deg, rgba(255,255,255,1) 0%, rgba(60,64,76,.25) 40%, rgba(20,22,28,.6) 100%);
  }
</style>
</head>
<body>

<section class="card card--front" aria-label="Business card front">
  <svg class="front-shape" viewBox="0 0 540 309" aria-hidden="true">
    <defs>
      <linearGradient id="headerGradient" x1="0" y1="0" x2="1" y2="0">
        <stop offset="0" stop-color="#7d8790"/>
        <stop offset=".45" stop-color="#1a1d21"/>
        <stop offset="1" stop-color="#050607"/>
      </linearGradient>
    </defs>
    <path d="M0 0 H540 V168 C440 152 300 136 130 131 L0 130 Z" fill="url(#headerGradient)"/>
    <path d="M130 131 C300 136 440 152 540 168 L540 194 C440 162 290 138 130 131 Z" fill="#ec5a10"/>
  </svg>
  <div class="front-illustration" role="img" aria-label="Illustration of a human back with the spine highlighted in orange"></div>
  <div class="company-name">Meridian Pain Care</div>

  <ul class="contact-list">
    <li><svg viewBox="0 0 10 10"><path d="M2 1h2l1 2-1.2 1a5 5 0 0 0 2.2 2.2L7 5l2 1v2a1 1 0 0 1-1 1A8 8 0 0 1 1 2a1 1 0 0 1 1-1z"/></svg>555.210.4481</li>
    <li><svg viewBox="0 0 10 10"><rect x="2" y="1" width="6" height="3"/><rect x="0.5" y="4" width="9" height="4" rx="1"/><rect x="2.5" y="7" width="5" height="2.5" fill="#fff"/></svg>555.210.4418</li>
    <li><svg viewBox="0 0 10 10"><circle cx="5" cy="5" r="4.5"/><circle cx="5" cy="5" r="1.6" fill="#fff"/></svg>www.meridianpaincare.com</li>
    <li><svg viewBox="0 0 10 10"><rect x="0.5" y="2" width="9" height="6.5"/><path d="M1 2.5 L5 5.8 L9 2.5" stroke="#fff" stroke-width="1" fill="none"/></svg>meridianpc.service@example.com</li>
  </ul>

  <div class="doctor">
    <div class="doctor-name">DR. LIANWEI ZHOU, M.D., PH.D</div>
    <div class="doctor-title">Board Certified Anesthiologist</div>
    <div class="address">18 Corvell Road, Suite 304<br>Brisdale, NJ 07391</div>
  </div>
</section>

<section class="card card--back" aria-label="Business card back">
  <div class="back-illustration" role="img" aria-label="Illustration of a human torso with the spine highlighted in orange"></div>
  <h2 class="appointment-title">APPOINTMENT</h2>
  <div class="field field--name">NAME:</div>
  <div class="field field--date">DATE :</div>
  <div class="field field--time">TIME :</div>
  <p class="notice">If unable to keep your appointment,please contact<br>us as soon as possible</p>
</section>

</body>
</html>
```